Harbor Crestline (Business Card Design)

Need business cards designed. Something modern, chic, and sleek. Mabye the back of the card should be the navy blue that is in the logo and then just the logo on the back.

Target Market(s)

Those in the hotel, office, and renovation industry

Contact Information for Business Card

1. Logo 2. Dorian Fenwick 3. CEO/Founder 4. Phone: (833) HarbCre / (833) 427-2731 5. Email: dorian@theharborcrestline.com 6. Website: www.theharborcrestline.com

Font styles to use
Other font styles liked:
• Look at the logo font and base the font for everything else off of that.

Colors
0054AA
0677BA
7BADD7
CADEEF
E8F1F8

Requirements
Must have
• Colors that are associated in the logo
Nice to have
• Sleek modern clean and chic design.

```html
<!DOCTYPE html>
<html lang="en">
<head>
<meta charset="utf-8">
<title>Harbor Crestline – Business Card</title>
<link href="https://fonts.googleapis.com/css2?family=Open+Sans:wght@400;600;700&display=swap" rel="stylesheet">
<style>
  :root {
    --backdrop: #2b2b2e;
    --navy: #0d1741;
    --gold: #c89b40;
    --white: #ffffff;
    --rule: rgba(255,255,255,0.45);
    --corner: #f2f2f2;
  }
  * { box-sizing: border-box; margin: 0; padding: 0; }
  html, body { width: 1200px; height: 780px; overflow: hidden; }
  body {
    background: var(--backdrop);
    font-family: "Open Sans", Arial, sans-serif;
    position: relative;
  }
  .card {
    position: absolute;
    width: 540px;
    height: 310px;
    background: var(--navy);
    border-radius: 3px;
    overflow: hidden;
    box-shadow: 0 14px 30px rgba(0,0,0,0.45);
  }
  .card--front { left: 40px; top: 235px; }
  .card--back  { left: 620px; top: 235px; }

  .brand {
    display: flex;
    align-items: center;
    gap: 10px;
    color: var(--white);
    font-weight: 700;
    text-transform: uppercase;
    letter-spacing: 0.12em;
  }
  .brand__mark { background: var(--gold); flex: none; }

  .card--front .brand {
    position: absolute;
    left: 36px; top: 100px;
    font-size: 17px;
    width: 200px;
    line-height: 1.25;
  }
  .card--front .brand__mark { width: 12px; height: 12px; }

  .divider {
    position: absolute;
    left: 252px; top: 70px;
    width: 1px; height: 150px;
    background: var(--rule);
    transform: rotate(20deg);
    transform-origin: center;
  }

  .person { position: absolute; left: 285px; top: 62px; }
  .person__name {
    font-size: 30px;
    font-weight: 700;
    line-height: 1.05;
    color: var(--white);
  }
  .person__first { color: var(--gold); }
  .person__title {
    font-size: 15px;
    color: var(--white);
    margin-top: 4px;
  }
  .contacts { list-style: none; margin-top: 14px; }
  .contacts li {
    display: flex; align-items: center; gap: 7px;
    font-size: 12px; color: var(--white);
    line-height: 1.6;
    white-space: nowrap;
  }
  .contacts svg { width: 11px; height: 11px; flex: none; fill: var(--gold); }

  .address-band {
    position: absolute;
    left: 0; bottom: 0;
    width: 100%; height: 38px;
    background: var(--gold);
    color: var(--white);
    font-size: 13px;
    display: flex; align-items: center;
    padding-left: 36px;
  }
  .corner {
    position: absolute;
    right: 0; bottom: 0;
    width: 110px; height: 38px;
    background: var(--navy);
    clip-path: polygon(22% 0, 100% 0, 100% 100%, 0 100%);
  }
  .corner__tab {
    position: absolute;
    right: 0; bottom: 0;
    width: 40px; height: 38px;
    background: var(--corner);
    clip-path: polygon(55% 0, 100% 0, 100% 100%, 0 100%);
  }

  .card--back .brand {
    position: absolute;
    left: 50%; top: 50%;
    transform: translate(-50%, -50%);
    font-size: 26px;
    white-space: nowrap;
    gap: 14px;
  }
  .card--back .brand__mark { width: 16px; height: 16px; }
</style>
</head>
<body>

  <section class="card card--front" aria-label="Business card front">
    <div class="brand">
      <span class="brand__mark"></span>
      <span class="brand__name">Harbor Crestline</span>
    </div>

    <div class="divider"></div>

    <div class="person">
      <h1 class="person__name"><span class="person__first">Dorian</span> Fenwick</h1>
      <p class="person__title">CEO/Founder</p>
      <ul class="contacts">
        <li>
          <svg viewBox="0 0 24 24" aria-hidden="true"><path d="M6.6 10.8a15.1 15.1 0 0 0 6.6 6.6l2.2-2.2c.3-.3.7-.4 1-.2 1.1.4 2.3.6 3.6.6.6 0 1 .4 1 1V20c0 .6-.4 1-1 1C10.6 21 3 13.4 3 4c0-.6.4-1 1-1h3.5c.6 0 1 .4 1 1 0 1.3.2 2.5.6 3.6.1.3 0 .7-.2 1z"/></svg>
          (833) HarbCre / (833) 427-2731
        </li>
        <li>
          <svg viewBox="0 0 24 24" aria-hidden="true"><path d="M12 2a10 10 0 1 0 0 20 10 10 0 0 0 0-20zm6.9 6h-2.9a15.7 15.7 0 0 0-1.4-3.6A8 8 0 0 1 18.9 8zM12 4c.8 1.2 1.5 2.5 1.9 4h-3.8c.4-1.5 1.1-2.8 1.9-4zM4.3 14a8 8 0 0 1 0-4h3.4a16.5 16.5 0 0 0 0 4zm.8 2h2.9c.3 1.3.8 2.5 1.4 3.6A8 8 0 0 1 5.1 16zM8 8H5.1a8 8 0 0 1 4.3-3.6C8.8 5.5 8.4 6.7 8 8zm4 12c-.8-1.2-1.5-2.5-1.9-4h3.8c-.4 1.5-1.1 2.8-1.9 4zm2.3-6H9.7a14.7 14.7 0 0 1 0-4h4.6a14.7 14.7 0 0 1 0 4zm.3 5.6c.6-1.1 1.1-2.3 1.4-3.6h2.9a8 8 0 0 1-4.3 3.6zm1.7-5.6a16.5 16.5 0 0 0 0-4h3.4a8 8 0 0 1 0 4z"/></svg>
          www.theharborcrestline.com
        </li>
        <li>
          <svg viewBox="0 0 24 24" aria-hidden="true"><path d="M3 5h18a1 1 0 0 1 1 1v12a1 1 0 0 1-1 1H3a1 1 0 0 1-1-1V6a1 1 0 0 1 1-1zm9 7.5L20 7H4zM4 9v8h16V9l-8 5.5z"/></svg>
          dorian@theharborcrestline.com
        </li>
      </ul>
    </div>

    <div class="address-band">4120 Linden Park Way Suite 210, Fairhaven, MD 21990</div>
    <div class="corner"></div>
    <div class="corner__tab"></div>
  </section>

  <section class="card card--back" aria-label="Business card back">
    <div class="brand">
      <span class="brand__mark"></span>
      <span class="brand__name">Harbor Crestline</span>
    </div>
  </section>

</body>
</html>
```